Ferncliff Capital - Website Design

We need a website design for a new commercial real estate company called Ferncliff Capital. We're effectively commercial mortgage brokers connecting real estate investors to lenders. We need a website that is simple (not busy), elegant, professional, and user-friendly. A lot of the users will be in their 50's and less tech savvy, so a stream-lined design is best. The website will serve as a portal for lenders to review new financing opportunities, as well as for real estate investors to review terms from lenders.
Updates
Just uploaded our logo.
Target Market(s)
Commercial real estate investors and lenders
Industry/Entity Type
Real Estate
Number of Pages Required
1 page
Colors
Designer to choose colors to be used in the design.
Look and feel

```html
<!DOCTYPE html>
<html lang="en">
<head>
<meta charset="utf-8">
<title>Ferncliff Capital</title>
<link href="https://fonts.googleapis.com/css2?family=Lato:wght@400;700&family=Open+Sans:wght@400;600;700&display=swap" rel="stylesheet">
<style>
:root{
  --teal:#1fa98b;
  --teal-dark:#178e74;
  --ink:#1b1b1b;
  --text:#6b6b6b;
  --grey-bg:#ececec;
  --field-border:#9a9a9a;
  --white:#ffffff;
}
*{margin:0;padding:0;box-sizing:border-box}
html,body{width:1200px;height:2862px;overflow:hidden}
body{position:relative;background:var(--white);font-family:"Open Sans",sans-serif;color:var(--text)}
.abs{position:absolute}
.brand{font-family:"Lato",sans-serif;font-weight:700;font-size:29px;color:var(--teal);display:flex;align-items:center;gap:10px}
.brand .mark{width:12px;height:12px;background:currentColor;display:inline-block}
.menu span{display:block;width:28px;height:4px;background:var(--teal);margin-bottom:5px;border-radius:1px}
.photo{position:absolute}
.hero{left:74px;top:71px;width:1052px;height:448px;background:linear-gradient(135deg,#e6e1d6 0%,#b7a894 40%,#6e5e4d 70%,#d8cfbf 100%)}
.hot-line{left:76px;top:242px;width:54px;height:3px;background:var(--teal)}
.hot-dot{left:122px;top:236px;width:15px;height:15px;border-radius:50%;background:var(--teal)}
.hot-label{left:153px;top:226px;font-family:"Lato",sans-serif;font-weight:700;font-size:30px;color:var(--teal)}
.price-tag{left:74px;top:280px;width:203px;height:63px;background:rgba(20,20,20,.88);color:var(--teal);font-family:"Lato",sans-serif;font-size:29px;display:flex;align-items:center;justify-content:center}
.dots{display:flex;gap:5px}
.dots i{width:9px;height:9px;border-radius:50%;border:1.5px solid #bbb;background:#fff;display:block}
.dots i.on{background:var(--teal);border-color:var(--teal)}
.h2{font-family:"Lato",sans-serif;font-weight:700;color:var(--ink);font-size:27px}
.para{font-size:12.5px;line-height:23px;color:var(--text)}
.about-text{font-size:11.2px;line-height:23px;width:498px;text-align:justify;letter-spacing:-.1px}
.btn{position:absolute;background:var(--teal);color:#fff;font-family:"Open Sans",sans-serif;font-weight:700;font-size:15px;display:flex;align-items:center;justify-content:center;letter-spacing:.3px}
.band{left:0;top:973px;width:1200px;height:450px;background:linear-gradient(180deg,#2cb596,#1fa98b)}
.band-title{left:0;width:1200px;text-align:center;font-family:"Lato",sans-serif;font-weight:700;font-size:37px;line-height:46px;color:#fff}
.band-copy{left:150px;width:900px;text-align:center;font-weight:600;font-size:20px;line-height:28px;color:#fff}
.quote-btn{left:515px;top:1231px;width:170px;height:47px;border:1.5px solid #fff;color:#fff;font-family:"Lato",sans-serif;font-weight:700;font-size:17px;display:flex;align-items:center;justify-content:center}
.card{position:absolute;top:1578px;width:306px;height:219px}
.card-label{position:absolute;left:0;width:100%;top:110px;text-align:center;color:#fff;font-family:"Lato",sans-serif;font-weight:700;font-size:22px}
.card-price{position:absolute;left:64px;bottom:0;width:226px;height:46px;background:rgba(30,30,30,.75);color:#fff;font-family:"Lato",sans-serif;font-weight:700;font-size:26px;display:flex;align-items:center;justify-content:center}
.arrow{position:absolute;top:1667px}
.grey{left:0;top:1935px;width:1200px;height:700px;background:var(--grey-bg)}
.field{position:absolute;border:1.5px solid var(--field-border);background:transparent;font-size:17px;color:#8c8c8c;padding:8px 16px}
.news-img{width:95px;height:88px}
.news-title{font-family:"Lato",sans-serif;font-weight:700;font-size:16px;color:var(--ink)}
.news-text{font-size:12.5px;line-height:23px;text-align:justify;width:281px}
.news-link{font-weight:700;font-size:13px;color:var(--teal)}
.footer{left:0;top:2500px;width:1200px;height:362px}
.foot-h{font-family:"Lato",sans-serif;font-weight:700;font-size:18px;color:#fff}
.foot-t{font-size:12.5px;line-height:23px;color:#fff}
.social{width:32px;height:32px;border-radius:50%;background:#fff}
</style>
</head>
<body>

<!-- Header -->
<div class="abs brand" style="left:99px;top:20px;"><span class="mark"></span>Ferncliff Capital</div>
<div class="abs menu" style="left:1075px;top:24px;"><span></span><span></span><span></span></div>

<!-- Hero -->
<div class="photo hero" role="img" aria-label="Couple meeting an adviser on a sofa in a bright living room"></div>
<div class="abs hot-line"></div>
<div class="abs hot-dot"></div>
<div class="abs hot-label">Hot Deal</div>
<div class="abs price-tag">$ 1, 12, 250</div>
<div class="abs dots" style="left:578px;top:479px;"><i class="on"></i><i></i><i></i><i></i></div>

<!-- About -->
<div class="photo" style="left:97px;top:597px;width:474px;height:292px;background:linear-gradient(120deg,#f2f1ee 0%,#cfd8dc 45%,#8fa3ad 75%,#e3e0da 100%)" role="img" aria-label="Agent shaking hands with a couple in a modern home"></div>
<div class="abs h2" style="left:609px;top:608px;">About Us</div>
<p class="abs para about-text" style="left:605px;top:651px;">Lorem Ipsum. Proin gravida nibh vel velit auctor aliquet. Aenean sollicitudin, ipsum, nec sagittis sem nibh id elit. Duis sed odio sit amet nibh vulputate cursus auctor a ornare odio. sed odio sit amet nibh vulputate cursus a sit amet mauris. Morbi accumsan. Lorem Ipsum. Proin gravida nibh vel velit auctor aliquetsem nibh id elit.</p>
<p class="abs para about-text" style="left:605px;top:760px;">Lorem Ipsum. Proin gravida nibh vel velit auctor aliquet. Aenean sollicitudin, ipsum, nec sagittis sem nibh id elit. Duis sed odio sit amet nibh vulputate cursus auctor a ornare odio. sed odio sit amet nibh vulputate cursus a sit amet mauris. Morbi accumsan.</p>
<div class="btn" style="left:603px;top:851px;width:116px;height:36px;">READ MORE</div>

<!-- Teal band -->
<div class="abs band" role="img" aria-label="Faded interior backdrop in teal"></div>
<svg class="abs" style="left:0;top:1320px" width="1200" height="110" viewBox="0 0 1200 110">
  <path d="M0 101 C 260 60, 560 0, 760 20 C 960 40, 1100 80, 1200 101 L1200 110 L0 110 Z" fill="#ffffff"/>
</svg>
<div class="abs band-title" style="top:1038px;">We Help real estate investors And lenders<br>Connect Each other</div>
<div class="abs band-copy" style="top:1139px;">Lorem Ipsum proin gravida nibh vel velit auctor aliquet. Aenean sollicitudin, ipsum, nec sagittis sem nibh id elit. Duis sed odio sit amet nibh vulputate cursus .</div>
<div class="abs quote-btn">Get A Quote</div>

<!-- Feature properties -->
<div class="abs h2" style="left:0;width:1200px;text-align:center;top:1492px;">Feature Properties</div>
<svg class="arrow" style="left:68px" width="16" height="20" viewBox="0 0 16 20"><path d="M12 3 L5 10 L12 17" stroke="#555" stroke-width="3" fill="none"/></svg>
<svg class="arrow" style="left:1116px" width="16" height="20" viewBox="0 0 16 20"><path d="M4 3 L11 10 L4 17" stroke="#555" stroke-width="3" fill="none"/></svg>

<div class="card" style="left:97px;">
  <div class="photo" style="inset:0;background:linear-gradient(135deg,#d9d6d0,#8f8a82 60%,#5f5a53)" role="img" aria-label="Luxury dining room interior"></div>
  <div class="card-label">LUXURY PARK CITY</div>
  <div class="btn" style="left:96px;top:160px;width:114px;height:31px;font-size:15px;font-weight:600;">VIEW MORE</div>
</div>
<div class="card" style="left:447px;">
  <div class="photo" style="inset:0;background:linear-gradient(180deg,#8fbde0 0%,#7e8d6a 45%,#6d6151 75%,#9a9185 100%)" role="img" aria-label="Suburban two-storey house with garden"></div>
  <div class="card-price">$ 1, 20, 500</div>
</div>
<div class="card" style="left:797px;">
  <div class="photo" style="inset:0;background:linear-gradient(180deg,#1f4fa8 0%,#3f6fc2 40%,#d9dde4 65%,#2a3d66 100%)" role="img" aria-label="Modern white villa at dusk"></div>
  <div class="card-price">$ 1, 20, 500</div>
</div>
<div class="abs dots" style="left:583px;top:1841px;gap:3px;"><i style="width:7px;height:7px;background:#666;border-color:#666"></i><i style="width:7px;height:7px"></i><i style="width:7px;height:7px"></i><i style="width:7px;height:7px"></i></div>

<!-- Contact & news -->
<div class="abs grey"></div>
<div class="abs h2" style="left:97px;width:529px;text-align:center;top:2005px;">Leave A Message</div>
<div class="field" style="left:97px;top:2076px;width:252px;height:38px;">Name</div>
<div class="field" style="left:374px;top:2076px;width:252px;height:38px;">Phone No</div>
<div class="field" style="left:97px;top:2137px;width:529px;height:38px;">Email</div>
<div class="field" style="left:97px;top:2200px;width:529px;height:181px;">Message</div>
<div class="btn" style="left:286px;top:2418px;width:151px;height:36px;">SEND MESSAGE</div>

<div class="abs h2" style="left:712px;top:2010px;">Latest News</div>

<div class="photo news-img" style="left:714px;top:2068px;background:linear-gradient(180deg,#cfe0ea,#8aa1b0 60%,#4d8fb5)" role="img" aria-label="Modern house with pool"></div>
<div class="abs news-title" style="left:820px;top:2069px;">Lorem Ipsum Is Simple</div>
<p class="abs para news-text" style="left:820px;top:2097px;">Lorem Ipsum. Proin gravida nibh vel velit auctor aliquet. Aenean sollicitudin, ipsum, nec sagittis sem nibh id elit. Duis sed odio sit.</p>
<div class="abs news-link" style="left:820px;top:2174px;">READ MORE</div>

<div class="photo news-img" style="left:714px;top:2259px;background:linear-gradient(135deg,#f3f1ee,#c9c2b8 60%,#8d8479)" role="img" aria-label="Two people reviewing documents"></div>
<div class="abs news-title" style="left:820px;top:2258px;">Lorem Ipsum Is Simple</div>
<p class="abs para news-text" style="left:820px;top:2286px;">Lorem Ipsum. Proin gravida nibh vel velit auctor aliquet. Aenean sollicitudin, ipsum, nec sagittis sem nibh id elit. Duis sed odio sit.</p>
<div class="abs news-link" style="left:820px;top:2363px;">READ MORE</div>
<div class="btn" style="left:883px;top:2418px;width:103px;height:36px;">VIEW ALL</div>

<!-- Footer -->
<svg class="abs footer" width="1200" height="362" viewBox="0 0 1200 362" role="img" aria-label="Faded house backdrop in teal">
  <defs>
    <linearGradient id="footGrad" x1="0" y1="0" x2="0" y2="1">
      <stop offset="0" stop-color="#27b193"/>
      <stop offset="1" stop-color="#1fa98b"/>
    </linearGradient>
  </defs>
  <path d="M0 104 C 200 60, 420 10, 640 12 C 880 14, 1060 30, 1200 8 L1200 362 L0 362 Z" fill="url(#footGrad)"/>
</svg>
<div class="abs brand" style="left:97px;top:2687px;color:#fff;"><span class="mark"></span>Ferncliff Capital</div>

<div class="abs foot-h" style="left:487px;top:2640px;">About</div>
<p class="abs foot-t" style="left:487px;top:2671px;width:234px;text-align:justify;">Lorem Ipsum. Proin gravida nibh vel velit auctor aliquet. Aenean sollicitudin, ipsum, nec sagittis sem sit.</p>

<div class="abs foot-h" style="left:788px;top:2638px;">Address</div>
<div class="abs foot-t" style="left:788px;top:2672px;font-size:11.5px;line-height:23px;">
  <div style="display:flex;align-items:center;gap:8px"><svg width="9" height="12" viewBox="0 0 9 12"><path d="M4.5 0 A4.5 4.5 0 0 1 9 4.5 C9 7.5 4.5 12 4.5 12 C4.5 12 0 7.5 0 4.5 A4.5 4.5 0 0 1 4.5 0 Z" fill="#fff"/><circle cx="4.5" cy="4.5" r="1.7" fill="#1fa98b"/></svg>Ferncliff Capital,</div>
  <div style="padding-left:17px">Lorem Ipsum.</div>
  <div style="display:flex;align-items:center;gap:8px"><svg width="10" height="10" viewBox="0 0 10 10"><path d="M2 0 L4 2.5 L3 4 C3.8 5.6 4.4 6.2 6 7 L7.5 6 L10 8 L8.5 10 C4 9.5 0.5 6 0 1.5 Z" fill="#fff"/></svg>(+1) 555 014 2290</div>
  <div style="display:flex;align-items:center;gap:8px"><svg width="10" height="8" viewBox="0 0 10 8"><rect width="10" height="8" fill="#fff"/><path d="M0 0 L5 4.5 L10 0" stroke="#1fa98b" fill="none"/></svg>mail@ferncliffcapital.com</div>
</div>

<div class="abs foot-h" style="left:975px;top:2638px;">Follow Us On</div>
<div class="abs social" style="left:980px;top:2680px;"></div>
<div class="abs social" style="left:1024px;top:2680px;"></div>
<div class="abs social" style="left:1070px;top:2680px;"></div>

<div class="abs" style="left:97px;top:2816px;width:1006px;height:1px;background:rgba(255,255,255,.55)"></div>
<div class="abs foot-t" style="left:0;width:1200px;text-align:center;top:2830px;font-size:13px;">Copyright © 2017 Ferncliff Capital. All Rights Reserved</div>

</body>
</html>
```